Investment company needing business card

We are wanting a business card which looks sharp and easy on the eye. We are thinking of having a business card with the logo embossed on it, to really make it stand out. We will only have a small amount of information of the business card, person's name, position, email address and phone number

Contact Information for Business Card

Danielle Frost
Executive Assistant
+64 21 473 5162
danielf@harwickpartners.co.nz

Requirements
Must have
• Embossed logo
Should not have
• Not to be busy

```html
<!DOCTYPE html>
<html lang="en">
<head>
<meta charset="utf-8">
<title>Harwick Partners — Business Card</title>
<link href="https://fonts.googleapis.com/css2?family=Open+Sans:wght@400;600;700&display=swap" rel="stylesheet">
<style>
  :root {
    --brand-green: #2bb673;
    --brand-green-deep: #23a065;
    --card-white: #ffffff;
    --ink-grey: #555a5e;
    --stage: #e9ebea;
  }
  * { box-sizing: border-box; margin: 0; padding: 0; }
  html, body {
    width: 1200px; height: 862px; overflow: hidden;
    background: var(--stage);
    font-family: "Open Sans", Arial, sans-serif;
  }
  .stage {
    position: relative; width: 1200px; height: 862px;
  }
  .card {
    position: absolute;
    width: 560px; height: 320px;
    border-radius: 26px;
    box-shadow: 0 6px 18px rgba(0,0,0,0.12);
  }
  /* Front */
  .card-front {
    left: 120px; top: 80px;
    background: var(--brand-green);
  }
  .brand-lockup {
    position: absolute; left: 0; right: 0; top: 118px;
    display: flex; align-items: center; justify-content: center; gap: 14px;
  }
  .brand-mark {
    width: 34px; height: 34px;
    background: var(--brand-green-deep);
  }
  .brand-name {
    color: var(--brand-green-deep);
    font-weight: 700; font-size: 34px; letter-spacing: 3px;
    text-transform: uppercase;
  }
  .front-web {
    position: absolute; left: 0; right: 0; bottom: 30px;
    text-align: center;
    color: var(--brand-green-deep);
    font-size: 13px; font-weight: 600; letter-spacing: 0.3px;
  }
  /* Back */
  .card-back {
    left: 520px; top: 462px;
    background: var(--card-white);
  }
  .back-content {
    position: absolute; left: 0; right: 0; top: 118px;
    display: flex; align-items: center; justify-content: center;
  }
  .person { text-align: right; padding-right: 18px; }
  .person-name {
    color: var(--brand-green);
    font-weight: 700; font-size: 25px; text-transform: uppercase;
    letter-spacing: 0.2px; line-height: 1.1;
  }
  .person-role {
    color: var(--ink-grey); font-size: 15px; margin-top: 4px;
  }
  .divider {
    width: 1.5px; height: 84px; background: var(--brand-green);
  }
  .contacts { list-style: none; padding-left: 16px; }
  .contacts li {
    display: flex; align-items: center; gap: 9px;
    color: var(--ink-grey); font-size: 13.5px; line-height: 24px;
  }
  .contacts svg { width: 13px; height: 13px; flex: none; }
</style>
</head>
<body>
<main class="stage">
  <section class="card card-front" aria-label="Card front">
    <div class="brand-lockup">
      <span class="brand-mark"></span>
      <span class="brand-name">Harwick Partners</span>
    </div>
    <p class="front-web">www.harwickpartners.co.nz</p>
  </section>

  <section class="card card-back" aria-label="Card back">
    <div class="back-content">
      <div class="person">
        <h1 class="person-name">Danielle Frost</h1>
        <p class="person-role">Executive Assistant</p>
      </div>
      <div class="divider"></div>
      <ul class="contacts">
        <li>
          <svg viewBox="0 0 16 16"><path fill="#2bb673" d="M3.6 1.2l2.3 2.6-1.3 1.6c.9 2 2.4 3.5 4.4 4.4l1.6-1.3 2.6 2.3-1.4 2.3C6.6 14.7 1.3 9.4 1.3 2.6z"/></svg>
          +64 21 473 5162
        </li>
        <li>
          <svg viewBox="0 0 16 16"><rect x="1.5" y="3.5" width="13" height="9" fill="none" stroke="#2bb673" stroke-width="1.5"/><path d="M1.5 3.5L8 9l6.5-5.5" fill="none" stroke="#2bb673" stroke-width="1.5"/></svg>
          danielf@harwickpartners.co.nz
        </li>
        <li>
          <svg viewBox="0 0 16 16"><circle cx="8" cy="8" r="6.5" fill="none" stroke="#2bb673" stroke-width="1.4"/><ellipse cx="8" cy="8" rx="2.8" ry="6.5" fill="none" stroke="#2bb673" stroke-width="1.2"/><path d="M1.5 8h13" stroke="#2bb673" stroke-width="1.2"/></svg>
          www.harwickpartners.co.nz
        </li>
      </ul>
    </div>
  </section>
</main>
</body>
</html>
```